Insurance Program Reusable Marketing Email Design

We need an email design that we can use for our marketing emails throughout the year. The design should be reusable (in general) for different product pushes and align with our brand www.norvelrisk.com. We are a property insurance program for the E&S market. Our program is available across the u.s. This is our 30th year in business and we want to portray ourself as experts in the field, being led by our years of data, focused on being modern and quick to respond to the market. Clean. Modern feel. We dont want an overwhelming amount of 'marketing' in the email or to come off too gimicky. It should work as an email that showcases new coverages or features & has space for information. Needs to work with Constant Contact

Target Market(s)

our appointed brokers - network of insurance professionals

Industry/Entity Type

insurance

Font styles to use
Sans Serif

Colors
0054AA
0677BA
7BADD7
CADEEF
E8F1F8
0094D4
00A9DD
6FCCEA
C7EBF8
E9F6FB

Requirements
Must have
• Work with Constant Contact style

```html
<!DOCTYPE html>
<html lang="en">
<head>
<meta charset="utf-8">
<title>Norvel Risk – Commercial Property Program</title>
<link href="https://fonts.googleapis.com/css2?family=Montserrat:wght@400;500;600;700&family=Open+Sans:wght@400;600&display=swap" rel="stylesheet">
<style>
:root{
  --accent:#2fa3dc;
  --accent-deep:#0677ba;
  --ink:#222629;
  --text:#33383c;
  --band:#cde6f5;
  --band-shape:#a8d7f1;
  --card:#ffffff;
  --footer:#2a2a2a;
  --footer-line:#454545;
  --white:#ffffff;
  --faint:#edf5fb;
}
*{margin:0;padding:0;box-sizing:border-box}
html,body{width:1200px;height:3214px;overflow:hidden;background:var(--white)}
body{position:relative;font-family:"Open Sans",Arial,sans-serif;color:var(--text)}
.abs{position:absolute}
.hero{left:0;top:0;width:1200px;height:553px;overflow:hidden}
.hero-photo{position:absolute;inset:0;background:linear-gradient(100deg,#c9c3b8 0%,#dcdcd8 30%,#e9edf0 55%,#f3f5f7 75%,#eceff2 100%)}
.hero-shape{position:absolute;left:0;top:0}
.brand{position:absolute;left:0;width:1200px;top:44px;display:flex;justify-content:center;align-items:center;gap:10px}
.brand-mark{width:18px;height:18px;background:var(--accent)}
.brand-name{font-family:"Montserrat",Arial,sans-serif;font-weight:700;font-size:38px;color:var(--ink);letter-spacing:-0.5px}
.hero-title{position:absolute;right:48px;top:178px;text-align:right;font-family:"Montserrat",Arial,sans-serif;font-weight:600;font-size:34px;line-height:48px;color:var(--ink)}
.hero-title .hl{color:var(--accent)}
.section-title{position:absolute;left:0;width:1200px;text-align:center;font-family:"Montserrat",Arial,sans-serif;font-weight:700;font-size:38px;letter-spacing:0.3px}
.rule{position:absolute;left:550px;width:100px;height:3px}
.coverage-title{top:648px;color:var(--accent)}
.coverage-rule{top:711px;background:#555}
.body-copy{position:absolute;left:45px;width:1110px;text-align:center;font-size:26px;line-height:48px;color:var(--text)}
.coverage-copy-1{top:758px}
.coverage-copy-2{top:923px}
.highlights{left:0;top:1187px;width:1200px;height:1085px;background:var(--band)}
.highlights-title{top:1267px;color:var(--ink)}
.highlights-rule{top:1327px;background:var(--accent)}
.card{position:absolute;top:1410px;width:260px;height:290px;background:var(--card);border-radius:8px;box-shadow:0 2px 10px rgba(0,80,140,.08);text-align:center}
.card svg{position:absolute;left:90px;top:36px}
.card p{position:absolute;left:10px;right:10px;top:138px;font-family:"Montserrat",Arial,sans-serif;font-size:22px;line-height:34px;color:var(--text)}
.list{position:absolute;top:1785px}
.list h3{font-family:"Montserrat",Arial,sans-serif;font-weight:600;font-size:26px;color:var(--ink);margin-bottom:20px}
.list li{list-style:none;position:relative;padding-left:35px;font-size:27px;line-height:39px;margin-bottom:6px;color:var(--text)}
.list li svg{position:absolute;left:0;top:11px}
.liability{left:47px}
.property{left:662px;width:500px}
.step-title{top:2346px;color:var(--accent)}
.step-rule{top:2409px;background:#555}
.step-copy{top:2456px}
.step-copy .hl{color:var(--accent)}
.badge{position:absolute;top:2662px;display:flex;align-items:center;gap:18px;font-size:31px;color:var(--ink)}
.footer{left:0;top:2817px;width:1200px;height:397px;background:var(--footer)}
.contact-title{top:2886px;color:var(--white)}
.contact-rule{top:2949px;background:var(--accent)}
.contact{position:absolute;top:3018px;font-family:"Montserrat",Arial,sans-serif;font-size:20px;line-height:33px;color:var(--white)}
.contact svg{position:absolute;top:0}
.footer-line{left:0;top:3145px;width:1200px;height:1px;background:var(--footer-line)}
.copyright{left:0;top:3171px;width:1200px;text-align:center;font-family:"Montserrat",Arial,sans-serif;font-size:20px;color:var(--white)}
.code{right:10px;top:3164px;font-family:"Montserrat",Arial,sans-serif;font-size:16px;color:var(--white)}
</style>
</head>
<body>

<header class="abs hero">
  <div class="hero-photo" role="img" aria-label="Photo of three smiling colleagues gathered around a laptop in a bright office"></div>
  <svg class="hero-shape" width="260" height="460" viewBox="0 0 260 460"><polygon points="0,0 0,300 230,300" fill="#2fa3dc" opacity=".9"/><polygon points="0,300 230,300 0,460" fill="#2fa3dc" opacity=".35"/></svg>
  <div class="brand"><span class="brand-mark"></span><span class="brand-name">Norvel Risk</span></div>
  <h1 class="hero-title">Empowering Property<br>Owners with <span class="hl">Data-driven</span><br><span class="hl">Commercial Insurance</span><br><span class="hl">Solutions</span></h1>
</header>

<svg class="abs" style="left:640px;top:905px" width="560" height="282" viewBox="0 0 560 282"><polygon points="280,0 0,282 280,282" fill="var(--faint)"/><polygon points="280,0 560,282 560,0" fill="#f4f9fc"/><rect x="280" y="0" width="0" height="0"/></svg>

<h2 class="section-title coverage-title">COVERAGE FEATURES</h2>
<div class="rule coverage-rule"></div>
<p class="body-copy coverage-copy-1">At Norvel Risk, we specialize in providing coverage for property owners in the E&amp;S commercial real estate industry. We understand that these industries require tailored coverage and have designed our programs to meet the specific needs of our clients.</p>
<p class="body-copy coverage-copy-2">We pride ourselves on the strength of our coverages and the ability to quickly shift to cater to the needs of the market and our clients. Our team of experienced professionals is always available to answer any questions and provide the right insurance solutions for your business.</p>

<section class="abs highlights"></section>
<svg class="abs" style="left:0;top:1992px" width="506" height="280" viewBox="0 0 506 280"><polygon points="225,0 0,225 0,280 225,280" fill="var(--band-shape)"/><polygon points="225,0 506,0 506,280" fill="var(--band-shape)"/><polygon points="225,0 506,280 225,280" fill="#bfe1f4"/></svg>

<h2 class="section-title highlights-title">HIGHLIGHTS</h2>
<div class="rule highlights-rule"></div>

<div class="card" style="left:45px">
  <svg width="80" height="80" viewBox="0 0 80 80" fill="none" stroke="#3a4248" stroke-width="2.5"><path d="M34 6 L60 16 V38 C60 56 48 66 34 72 C20 66 8 56 8 38 V16 Z"/><path d="M34 14 L52 21 V38 C52 51 44 58 34 63 C24 58 16 51 16 38 V21 Z"/><circle cx="34" cy="38" r="11"/><path d="M37 32 H32 a3 3 0 0 0 0 6 h4 a3 3 0 0 1 0 6 H31 M34 29 V47"/><circle cx="57" cy="60" r="9" fill="#fff"/><path d="M53 56 L61 64 M61 56 L53 64"/></svg>
  <p>No<br>Co-Insurance</p>
</div>
<div class="card" style="left:329px">
  <svg width="80" height="80" viewBox="0 0 80 80" fill="none" stroke="#3a4248" stroke-width="2.5"><rect x="8" y="14" width="58" height="50" rx="3"/><path d="M8 26 H66 M20 8 V18 M34 8 V18 M48 8 V18 M60 8 V18"/><rect x="16" y="32" width="8" height="6"/><rect x="28" y="32" width="8" height="6"/><rect x="40" y="32" width="8" height="6"/><rect x="52" y="32" width="8" height="6"/><rect x="16" y="44" width="8" height="6"/><rect x="28" y="44" width="8" height="6"/><rect x="40" y="44" width="8" height="6"/><circle cx="62" cy="62" r="11" fill="#fff"/><path d="M62 56 V62 L66 65"/></svg>
  <p>180 days<br>Extended Period<br>of Indemnity</p>
</div>
<div class="card" style="left:612px">
  <svg width="80" height="80" viewBox="0 0 80 80" fill="none" stroke="#3a4248" stroke-width="2.5"><path d="M6 26 L40 8 L74 26 Z"/><path d="M10 30 H70 M10 64 H70 M6 70 H74"/><path d="M18 34 V60 M26 34 V60 M36 34 V60 M44 34 V60 M54 34 V60 M62 34 V60"/></svg>
  <p>Building<br>Ordinance or Law<br>included</p>
</div>
<div class="card" style="left:896px">
  <svg width="80" height="80" viewBox="0 0 80 80" fill="none" stroke="#3a4248" stroke-width="2.5"><path d="M6 38 L40 8 L74 38"/><path d="M14 32 V70 H66 V32"/><path d="M56 10 H64 V24"/><circle cx="40" cy="40" r="7"/><path d="M28 62 C28 52 34 48 40 48 C46 48 52 52 52 62 Z"/></svg>
  <p>$100,000 Tenant<br>Relocation<br>Expense included</p>
</div>

<div class="list liability">
  <h3>Liability features:</h3>
  <ul>
    <li><svg width="22" height="22" viewBox="0 0 22 22"><circle cx="11" cy="11" r="9" fill="none" stroke="var(--accent)" stroke-width="2.5"/><path d="M6.5 11 L9.8 14 L15.5 8" fill="none" stroke="var(--accent)" stroke-width="2.5"/></svg>Per Location Aggregate</li>
    <li><svg width="22" height="22" viewBox="0 0 22 22"><circle cx="11" cy="11" r="9" fill="none" stroke="var(--accent)" stroke-width="2.5"/><path d="M6.5 11 L9.8 14 L15.5 8" fill="none" stroke="var(--accent)" stroke-width="2.5"/></svg>Hired &amp; Non Owned Auto</li>
  </ul>
</div>
<div class="list property">
  <h3>Included in Real Property:</h3>
  <ul>
    <li><svg width="22" height="22" viewBox="0 0 22 22"><circle cx="11" cy="11" r="9" fill="none" stroke="var(--accent)" stroke-width="2.5"/><path d="M6.5 11 L9.8 14 L15.5 8" fill="none" stroke="var(--accent)" stroke-width="2.5"/></svg>Outdoor Fences, Signs</li>
    <li><svg width="22" height="22" viewBox="0 0 22 22"><circle cx="11" cy="11" r="9" fill="none" stroke="var(--accent)" stroke-width="2.5"/><path d="M6.5 11 L9.8 14 L15.5 8" fill="none" stroke="var(--accent)" stroke-width="2.5"/></svg>Roadways, Walks, Patios, Paved Surfaces</li>
    <li><svg width="22" height="22" viewBox="0 0 22 22"><circle cx="11" cy="11" r="9" fill="none" stroke="var(--accent)" stroke-width="2.5"/><path d="M6.5 11 L9.8 14 L15.5 8" fill="none" stroke="var(--accent)" stroke-width="2.5"/></svg>Retaining Walls that are not part of the building</li>
    <li><svg width="22" height="22" viewBox="0 0 22 22"><circle cx="11" cy="11" r="9" fill="none" stroke="var(--accent)" stroke-width="2.5"/><path d="M6.5 11 L9.8 14 L15.5 8" fill="none" stroke="var(--accent)" stroke-width="2.5"/></svg>Foundations of Buildings &amp; Structures below Basement</li>
    <li><svg width="22" height="22" viewBox="0 0 22 22"><circle cx="11" cy="11" r="9" fill="none" stroke="var(--accent)" stroke-width="2.5"/><path d="M6.5 11 L9.8 14 L15.5 8" fill="none" stroke="var(--accent)" stroke-width="2.5"/></svg>Underground Pipes, Flues or Drains</li>
  </ul>
</div>

<h2 class="section-title step-title">A&nbsp; STEP ABOVE</h2>
<div class="rule step-rule"></div>
<p class="body-copy step-copy"><span class="hl">Our vision</span> of bringing tailored solutions to property owners and managers continues to live on today as we strive to be adaptive and responsive to the needs of the market and our clients.</p>

<div class="badge" style="left:138px">
  <svg width="62" height="66" viewBox="0 0 62 66" fill="none" stroke="#3a4248" stroke-width="2.2"><circle cx="31" cy="26" r="22"/><circle cx="31" cy="26" r="15"/><path d="M31 16 L34 23 L41 23 L35.5 27.5 L37.5 34.5 L31 30 L24.5 34.5 L26.5 27.5 L21 23 L28 23 Z"/><path d="M18 44 L12 62 L20 58 L24 64 L29 48 M44 44 L50 62 L42 58 L38 64 L33 48"/></svg>
  <span>Exclusive Appointments</span>
</div>
<div class="badge" style="left:648px">
  <svg width="64" height="66" viewBox="0 0 64 66" fill="none" stroke="#3a4248" stroke-width="2.2"><path d="M14 4 L16 9 L21 9 L17 12 L18.5 17 L14 14 L9.5 17 L11 12 L7 9 L12 9 Z M32 2 L34 7 L39 7 L35 10 L36.5 15 L32 12 L27.5 15 L29 10 L25 7 L30 7 Z M50 4 L52 9 L57 9 L53 12 L54.5 17 L50 14 L45.5 17 L47 12 L43 9 L48 9 Z"/><rect x="4" y="38" width="12" height="24"/><path d="M16 40 L28 26 L30 20 C34 20 36 24 35 30 L33 36 H52 C56 36 58 40 56 43 C58 45 57 49 54 50 C56 53 54 56 51 57 C52 60 50 62 46 62 H16"/></svg>
  <span>30 Years in Business</span>
</div>

<footer class="abs footer"></footer>
<h2 class="section-title contact-title">CONTACT US</h2>
<div class="rule contact-rule"></div>

<div class="contact" style="left:48px">
  <svg width="42" height="42" viewBox="0 0 42 42" fill="none" stroke="#fff" stroke-width="2"><path d="M8 4 L15 4 L18 13 L13 17 C15 23 19 27 25 29 L29 24 L38 27 V34 C38 36 36 38 34 38 C18 37 5 24 4 8 C4 6 6 4 8 4 Z"/><path d="M24 4 C31 5 37 11 38 18 M24 10 C28 11 31 14 32 18"/></svg>
  <div style="margin-left:62px">PHONE: 555.214.7300<br>FAX: 555.214.7311</div>
</div>
<div class="contact" style="left:396px">
  <svg width="46" height="32" viewBox="0 0 46 32" fill="none" stroke="#fff" stroke-width="2"><rect x="2" y="2" width="42" height="28"/><path d="M2 2 L23 19 L44 2 M2 30 L17 14 M44 30 L29 14"/></svg>
  <div style="margin-left:62px;margin-top:-5px">customerservice@norvelrisk.com</div>
</div>
<div class="contact" style="left:886px">
  <svg width="30" height="42" viewBox="0 0 30 42" fill="none" stroke="#fff" stroke-width="2"><path d="M15 40 C15 40 3 25 3 15 A12 12 0 0 1 27 15 C27 25 15 40 15 40 Z"/><circle cx="15" cy="15" r="5"/></svg>
  <div style="margin-left:56px">1480 W. Harbor Street,<br>Suite 400<br>Riverton, CA 91580</div>
</div>

<div class="abs footer-line"></div>
<p class="abs copyright">2024 Norvel Risk Services, Inc. Al Rights Reserved.</p>
<p class="abs code">C50</p>

</body>
</html>
```